Tolbek cards

I want a simple business card that pops.
Logo on one side.
On side two i want.
"Are you thinking about a new building on your property, or renovating an existing structure? Contact".....
Owners Name: Dale Whitacre
Owners Phone number: 610-555-0187
Address:4076 Copper Ridge RD, Kestrow, PA 16830
Committed to Quality, Service, and Integrity

```html
<!DOCTYPE html>
<html lang="en">
<head>
<meta charset="utf-8">
<title>Tolbek Business Card</title>
<link rel="stylesheet" href="https://fonts.googleapis.com/css2?family=Montserrat:wght@400;500;600;700;800&display=swap">
<style>
  :root {
    --page-bg: #ecebe8;
    --card-white: #ffffff;
    --brown-deep: #42301d;
    --brown-dark: #4a2e1a;
    --brown-light: #9a8468;
    --text-dark: #3b2617;
    --text-light: #ffffff;
  }
  * { margin: 0; padding: 0; box-sizing: border-box; }
  html, body {
    width: 1181px;
    height: 1200px;
    overflow: hidden;
    background: var(--page-bg);
    font-family: "Montserrat", sans-serif;
  }
  .card {
    position: absolute;
    left: 221px;
    width: 745px;
    height: 425px;
    box-shadow: 0 6px 18px rgba(0,0,0,0.18);
  }
  .card-front { top: 126px; background: var(--card-white); }
  .card-back  { top: 658px; background: var(--brown-deep); }

  .top-band {
    position: absolute; left: 0; top: 0; width: 100%; height: 26px;
    background: linear-gradient(90deg, var(--brown-dark) 0%, #6a4f35 55%, var(--brown-light) 100%);
  }
  .bottom-band {
    position: absolute; left: 0; top: 372px; width: 100%; height: 53px;
    background: linear-gradient(90deg, var(--brown-dark) 0%, #6a4f35 60%, var(--brown-light) 100%);
    display: flex; align-items: center; justify-content: center;
  }
  .tagline {
    color: var(--text-light);
    font-size: 22px;
    font-weight: 400;
    letter-spacing: 1.6px;
  }
  .brand-name {
    position: absolute; left: 20px; width: 240px; top: 172px;
    text-align: center;
    font-size: 40px; font-weight: 800;
    color: var(--text-dark);
    letter-spacing: 0.5px;
  }
  .divider {
    position: absolute; left: 269px; top: 59px;
    width: 3px; height: 269px;
    background: var(--text-dark);
  }
  .owner-name {
    position: absolute; left: 305px; top: 52px;
    font-size: 31px; font-weight: 600; color: var(--text-dark);
  }
  .owner-title {
    position: absolute; left: 310px; top: 100px;
    font-size: 11px; font-weight: 500; letter-spacing: 1px;
    color: var(--text-dark);
  }
  .contact-row {
    position: absolute; left: 305px;
    display: flex; align-items: flex-start;
    font-size: 20px; color: var(--text-dark); line-height: 25px;
  }
  .contact-row svg { width: 26px; height: 26px; margin-right: 16px; flex: none; }
  .contact-phone { top: 136px; }
  .contact-address { top: 176px; }
  .pitch {
    position: absolute; left: 347px; top: 245px;
    font-size: 20px; line-height: 25px; color: var(--text-dark);
  }
  .back-brand {
    position: absolute; left: 0; top: 0; width: 100%; height: 100%;
    display: flex; align-items: center; justify-content: center;
    font-size: 84px; font-weight: 800; color: var(--text-light);
    letter-spacing: 1px;
  }
</style>
</head>
<body>
  <section class="card card-front">
    <div class="top-band"></div>
    <div class="brand-name">Tolbek</div>
    <div class="divider"></div>
    <h1 class="owner-name">Dale Whitacre</h1>
    <p class="owner-title">COSMETIC AND FAMILY DENTISTRY</p>
    <div class="contact-row contact-phone">
      <svg viewBox="0 0 24 24" aria-hidden="true">
        <circle cx="12" cy="12" r="12" fill="#3b2617"/>
        <path d="M8.2 5.8c.5-.3 1.1-.2 1.4.3l1.2 2.1c.3.5.2 1.1-.3 1.4l-.8.5c.6 1.5 1.7 2.7 3.2 3.4l.5-.8c.3-.5.9-.6 1.4-.3l2.1 1.2c.5.3.6.9.3 1.4l-.8 1.2c-.5.7-1.4 1-2.2.7-3.3-1.2-5.9-3.8-7.1-7.1-.3-.8 0-1.7.7-2.2z" fill="#fff"/>
      </svg>
      <span>610-555-0187</span>
    </div>
    <div class="contact-row contact-address">
      <svg viewBox="0 0 24 24" aria-hidden="true" style="margin-top:6px">
        <circle cx="12" cy="12" r="12" fill="#3b2617"/>
        <path d="M12 5a4.5 4.5 0 0 0-4.5 4.5c0 3.3 4.5 8.5 4.5 8.5s4.5-5.2 4.5-8.5A4.5 4.5 0 0 0 12 5zm0 6.3a1.8 1.8 0 1 1 0-3.6 1.8 1.8 0 0 1 0 3.6z" fill="#fff"/>
      </svg>
      <span>4076 Copper Ridge RD, Kestrow,<br>PA 16830</span>
    </div>
    <p class="pitch">Are you thinking about a new<br>building on your property, or reno-<br>vating an existing structure? Con-<br>tact</p>
    <div class="bottom-band"><span class="tagline">Committed to Quality, Service, and Integrity</span></div>
  </section>

  <section class="card card-back">
    <div class="back-brand">Tolbek</div>
  </section>
</body>
</html>
```